business card deign

Logo needs the following on it.
1. attached logo
2. Tagline - "If it keeps a drink cold or the party going...we do it!"
3. Name- Dalton Pikes, Founder and CPO
4. Address - 412 E. Carver Avenue, Ste 2207, Tampa, FL. 33917
5. Phone - 555.318.4726

```html
<!DOCTYPE html>
<html lang="en">
<head>
<meta charset="utf-8">
<title>Brimway Business Card</title>
<link rel="stylesheet" href="https://fonts.googleapis.com/css2?family=Roboto:wght@400;500;700;900&display=swap">
<style>
  :root {
    --stage: #262626;
    --card-dark: #111111;
    --card-light: #ffffff;
    --ink: #0d0d0d;
    --ink-soft: #2a2a2a;
    --silver: #d9d9d9;
    --pattern-hi: #5a5a5a;
    --pattern-lo: #151515;
  }
  * { box-sizing: border-box; margin: 0; padding: 0; }
  html, body {
    width: 1200px; height: 780px; overflow: hidden;
    background: var(--stage);
    font-family: "Roboto", Arial, sans-serif;
  }
  .canvas { position: relative; width: 1200px; height: 780px; }

  .card {
    position: absolute;
    width: 560px; height: 320px;
    border-radius: 26px;
    overflow: hidden;
    box-shadow: 0 14px 30px rgba(0,0,0,0.55);
  }

  /* Back side */
  .card-back { left: 50px; top: 70px; background: var(--card-dark); }
  .back-pattern {
    position: absolute; inset: 0;
    background: linear-gradient(200deg, var(--pattern-hi) 0%, #2a2a2a 35%, var(--pattern-lo) 75%);
  }
  .back-mark {
    position: absolute; right: 70px; top: 150px;
    display: flex; flex-direction: column; align-items: center; gap: 6px;
    color: var(--silver);
  }
  .back-mark .dot { width: 14px; height: 14px; border-radius: 50%; background: var(--silver); }
  .back-mark .word { font-size: 9px; font-weight: 700; letter-spacing: 3px; }

  /* Front side */
  .card-front { left: 590px; top: 390px; background: var(--card-light); color: var(--ink); }
  .brand {
    position: absolute; left: 40px; top: 110px; width: 200px;
    display: flex; flex-direction: column; align-items: center; gap: 16px;
  }
  .brand .dot { width: 64px; height: 64px; border-radius: 50%; background: var(--ink); }
  .brand .word { font-size: 28px; font-weight: 900; letter-spacing: 9px; }

  .divider {
    position: absolute; left: 268px; top: 58px;
    width: 1px; height: 150px; background: var(--ink-soft);
  }

  .details { position: absolute; left: 300px; top: 62px; }
  .details .name { font-size: 28px; font-weight: 900; letter-spacing: -0.3px; line-height: 1; }
  .details .title { font-size: 15px; font-weight: 500; margin-top: 6px; }
  .contact { list-style: none; margin-top: 18px; font-size: 13px; line-height: 1.35; }
  .contact li { display: flex; align-items: flex-start; gap: 8px; margin-bottom: 3px; }
  .contact svg { width: 13px; height: 13px; flex: none; margin-top: 2px; }

  .tagline {
    position: absolute; left: 0; right: 0; bottom: 40px;
    text-align: center; font-size: 14px; font-weight: 500;
  }
</style>
</head>
<body>
<main class="canvas">
  <section class="card card-back" aria-label="Card back">
    <div class="back-pattern" role="img" aria-label="Repeating brand mark pattern in graded silver on black"></div>
    <div class="back-mark">
      <span class="dot"></span>
      <span class="word">BRIMWAY</span>
    </div>
  </section>

  <section class="card card-front" aria-label="Card front">
    <div class="brand">
      <span class="dot"></span>
      <span class="word">BRIMWAY</span>
    </div>
    <div class="divider"></div>
    <div class="details">
      <h1 class="name">Dalton Pikes</h1>
      <p class="title">Founder and CPO</p>
      <ul class="contact">
        <li>
          <svg viewBox="0 0 24 24" aria-hidden="true"><path fill="currentColor" d="M6.6 10.8a15.1 15.1 0 0 0 6.6 6.6l2.2-2.2a1 1 0 0 1 1-.25 11.4 11.4 0 0 0 3.6.57 1 1 0 0 1 1 1V20a1 1 0 0 1-1 1A17 17 0 0 1 3 4a1 1 0 0 1 1-1h3.5a1 1 0 0 1 1 1c0 1.25.2 2.45.57 3.57a1 1 0 0 1-.25 1z"/></svg>
          <span>555.318.4726</span>
        </li>
        <li>
          <svg viewBox="0 0 24 24" aria-hidden="true"><path fill="none" stroke="currentColor" stroke-width="2.2" d="M12 22s7-7.2 7-12.5a7 7 0 0 0-14 0C5 14.8 12 22 12 22z"/><circle cx="12" cy="9.5" r="2.6" fill="currentColor"/></svg>
          <span>412 E. Carver Avenue,<br>Ste 2207, Tampa, FL. 33917</span>
        </li>
      </ul>
    </div>
    <p class="tagline">If it keeps a drink cold or the party going...we do it!</p>
  </section>
</main>
</body>
</html>
```